Presentation and Communication Coaching Services Business needs updated interactive web site

I want to keep the color scheme, functionality, and pages of my current site, but with a newer/updated look. I need to improve security and simplify images, etc. (Please see current site http://brightwellvoicetutor.com ) This will need be functional on mobile devices, as well.

I'm attached to the scrolling client list and scrolling client feedback.

Industry/Entity Type

Professional Service

Font styles to use
Sans Serif

Colors
0356a4
f37122
33a6d7

Requirements
Must have
• scrolling client banner on home page, client comments slider, color scheme
• Please see current site: http://brightwellvoicetutor.com
Nice to have
• better action/appearance
Should not have
• I don't want it to look like all the other sites/templates

```html
<!DOCTYPE html>
<html lang="en">
<head>
<meta charset="utf-8">
<title>Brightwell Voice Tutoring</title>
<link href="https://fonts.googleapis.com/css2?family=Josefin+Sans:wght@400;600;700&family=Montserrat:wght@500;600;700;800&display=swap" rel="stylesheet">
<style>
:root{
  --blue:#0356a4;
  --navy:#0b3f86;
  --orange:#f37122;
  --sky:#33a6d7;
  --ink:#1c1c1c;
  --text:#444;
  --pale:#e7f1fb;
  --footer:#121212;
  --white:#fff;
}
*{margin:0;padding:0;box-sizing:border-box}
html,body{width:1200px;height:4206px;overflow:hidden;background:var(--white)}
body{position:relative;font-family:"Josefin Sans",sans-serif;color:var(--text)}
.abs{position:absolute}

/* header */
.brand{left:112px;top:30px;font-size:27px;color:#222;letter-spacing:.2px}
.contact-chip{top:26px;display:flex;align-items:center;gap:14px}
.contact-chip .ico{width:44px;height:44px;border-radius:50%;background:var(--blue);display:flex;align-items:center;justify-content:center}
.contact-chip small{display:block;font-size:14px;color:#333}
.contact-chip strong{display:block;font-size:16px;color:var(--blue);font-weight:700}
.nav{left:112px;top:93px;width:973px;height:53px;border-radius:27px;background:var(--sky);display:flex;align-items:center;overflow:hidden;z-index:3}
.nav a{color:#fff;text-decoration:none;font-size:15px;font-weight:600;margin-left:36px}
.nav a:first-child{margin-left:56px}
.nav .login{margin-left:auto;background:var(--navy);height:100%;width:191px;display:flex;align-items:center;justify-content:center;font-size:18px;font-weight:700;border-radius:0 27px 27px 0}

/* hero */
.hero{left:0;top:118px;width:1200px;height:602px;background:linear-gradient(180deg,#eef0f2 0%,#d9dcdf 55%,#8c8278 100%)}
.hero h1{position:absolute;top:160px;width:100%;text-align:center;font-family:"Montserrat",sans-serif;font-weight:600;font-size:45px;line-height:58px;color:var(--blue)}
.hero p{position:absolute;top:290px;width:100%;text-align:center;font-size:21px;line-height:30px;color:#222}
.btn{display:flex;align-items:center;justify-content:center;color:#fff;font-weight:700;text-decoration:none;white-space:nowrap}
.hero .btn{position:absolute;left:499px;top:376px;width:202px;height:56px;background:var(--blue);font-size:20px}
.arrow{width:56px;height:56px;border-radius:50%;background:#fff;display:flex;align-items:center;justify-content:center}

/* feature strip */
.strip{top:717px;height:6px}
.feature{top:678px;width:300px;text-align:center}
.feature .ring{width:84px;height:84px;margin:0 auto;border-radius:50%;background:#fff;border:4px solid;display:flex;align-items:center;justify-content:center}
.feature small{display:block;margin-top:24px;font-size:17px;color:#444}
.feature b{display:block;margin-top:6px;font-size:19px;font-weight:700;letter-spacing:.5px}

/* about */
.about-photo{left:112px;top:962px;width:485px;height:328px;background:linear-gradient(120deg,#f3f3f3,#c9ced3 60%,#7b8694)}
.about-frame{left:597px;top:1055px;width:14px;height:245px;background:var(--sky)}
.about-frame-b{left:190px;top:1286px;width:421px;height:12px;background:var(--sky)}
.person-name{left:194px;top:1328px;font-size:27px;font-weight:700;color:#222}
.person-role{left:194px;top:1366px;font-size:15px;color:#666}
.section-title{font-family:"Montserrat",sans-serif;font-weight:700;color:#111;letter-spacing:1px}
.about-title{left:653px;top:984px;font-size:37px}
.about-copy{left:653px;top:1056px;width:432px;font-size:14px;line-height:20px;text-align:justify;color:#333}
.about-copy p+p{margin-top:12px}
.about-btn{left:653px;top:1321px;width:205px;height:56px;background:var(--blue);font-size:18px}

/* services */
.services{left:0;top:1503px;width:1200px;height:670px;background:var(--pale)}
.services-title{top:1596px;width:1200px;text-align:center;font-size:35px}
.svc h3{font-family:"Montserrat",sans-serif;font-weight:700;font-size:27px;letter-spacing:.5px}
.svc p{font-size:14.5px;line-height:29px;color:#444;margin-top:8px}
.svc.right-align{text-align:right}
.hub{left:520px;top:1816px;width:160px;height:160px;border-radius:50%;background:var(--sky);border:6px solid #fff;box-shadow:0 0 0 8px var(--blue);display:flex;flex-direction:column;align-items:center;justify-content:center;color:#fff}
.hub b{font-size:26px;font-weight:600}
.hub span{font-size:12px}
.dot{width:34px;height:34px;border-radius:50%;border:4px solid;background:#fff;display:flex;align-items:center;justify-content:center}
.dot i{width:14px;height:14px;border-radius:50%;display:block}

/* voiceover */
.voice{left:0;top:2173px;width:1200px;height:393px;background:linear-gradient(90deg,#0a4e9c,#0a62b8 50%,#0b4e98)}
.voice-title{width:1200px;text-align:center;color:#fff;font-size:37px}
.voice-copy{width:1200px;text-align:center;color:#fff;font-size:21px;line-height:34px}
.voice .btn{height:60px;font-size:16px;font-weight:600;letter-spacing:.2px}

/* training */
.train-title{left:112px;top:2665px;width:500px;font-size:33px;line-height:48px;letter-spacing:0;color:#111;white-space:nowrap}
.train-list{left:140px;top:2785px;list-style:none;font-size:16px;color:#333}
.train-list li{height:36.8px}
.video-frame{left:636px;top:2698px;width:463px;height:304px;background:var(--sky)}
.video{left:622px;top:2678px;width:463px;height:308px;background:linear-gradient(135deg,#d7cfc4,#9a8d7e 55%,#5c5047)}

/* partners */
.partners{left:0;top:3107px;width:1200px;height:348px;background:var(--pale)}
.partners-title{top:3165px;width:1200px;text-align:center;font-size:35px}
.logo-card{top:3261px;width:188px;height:118px;background:#fff;display:flex;align-items:center;justify-content:center;gap:10px;font-family:"Josefin Sans",sans-serif;font-weight:700;font-size:24px;color:var(--blue);box-shadow:0 2px 6px rgba(0,0,0,.08)}
.logo-card i{width:14px;height:14px;border-radius:50%;background:var(--blue);display:block}
.slide-arrow{width:52px;height:52px;border-radius:50%;background:var(--blue);display:flex;align-items:center;justify-content:center}

/* reviews */
.reviewer{left:163px;top:3545px;width:190px;height:190px;border-radius:50%;border:5px solid var(--blue);background:linear-gradient(160deg,#e8edf2,#a9b5c2)}
.quote{left:272px;top:3528px;width:56px;height:56px;border-radius:50%;background:var(--blue);border:4px solid #fff;color:#fff;font-family:"Montserrat",sans-serif;font-size:38px;font-weight:800;text-align:center;line-height:62px}
.review-title{left:401px;top:3538px;font-size:37px}
.review-copy{left:401px;top:3596px;width:684px;font-size:14px;line-height:25px;text-align:justify;color:#333}
.review-name{left:408px;top:3742px;font-family:"Montserrat",sans-serif;font-size:21px;font-weight:700;color:var(--blue)}
.review-role{left:408px;top:3774px;font-size:13px;color:#555}
.review-rule{left:665px;top:3740px;width:1px;height:54px;background:#ccc}
.review-brand{left:709px;top:3756px;display:flex;align-items:center;gap:10px;font-size:20px;font-weight:700;color:#7a2a8e}
.review-brand i{width:16px;height:16px;background:#7a2a8e;display:block}
.pager{top:3779px;width:14px;height:14px;border-radius:50%;border:2px solid #777}

/* footer */
.footer{left:0;top:3870px;width:1200px;height:336px;background:var(--footer);color:#fff}
.footer h4{position:absolute;top:50px;font-family:"Montserrat",sans-serif;font-size:25px;font-weight:700}
.footer .col-text{position:absolute;font-size:15px;line-height:23px}
.footer .rule{position:absolute;left:112px;top:260px;width:973px;height:1px;background:#3a3a3a}
.footer .legal{position:absolute;top:284px;font-size:13px;color:#ddd}
.f-item{position:absolute;display:flex;gap:20px;font-size:15px;line-height:23px}
</style>
</head>
<body>

<!-- header -->
<div class="abs brand">brightwellvoicetutoring</div>
<div class="abs contact-chip" style="left:543px">
  <span class="ico"><svg width="22" height="22" viewBox="0 0 24 24"><path fill="#fff" d="M6.6 10.8a15.1 15.1 0 0 0 6.6 6.6l2.2-2.2c.3-.3.7-.4 1-.2 1.1.4 2.3.6 3.6.6.6 0 1 .4 1 1V20c0 .6-.4 1-1 1A17 17 0 0 1 3 4c0-.6.4-1 1-1h3.5c.6 0 1 .4 1 1 0 1.3.2 2.5.6 3.6.1.3 0 .7-.2 1z"/></svg></span>
  <span><small>Call Us</small><strong>718.555.0143</strong></span>
</div>
<div class="abs contact-chip" style="left:756px">
  <span class="ico"><svg width="22" height="22" viewBox="0 0 24 24"><rect x="3" y="6" width="18" height="12" rx="1.5" fill="#fff"/><path d="M3.5 6.8 12 13l8.5-6.2" stroke="#0356a4" stroke-width="1.6" fill="none"/></svg></span>
  <span><small>Email Us</small><strong>info@brightwellvoicetutor.com</strong></span>
</div>
<nav class="abs nav">
  <a href="#">Home</a><a href="#">About</a><a href="#">Clients</a><a href="#">Reviews</a><a href="#">Services</a><a href="#">Contact</a><a href="#">Speaking Secrets</a>
  <a href="#" class="login">CLIENT LOGIN</a>
</nav>

<!-- hero -->
<section class="abs hero" role="img" aria-label="Photo of a coach presenting to a seated audience in a bright seminar room">
  <h1>You’re good at what you do.<br>Learn How to let it show.</h1>
  <p>An individual works hard to reach a place of respect and<br>authority in her or his chosen profession.</p>
  <a href="#" class="btn">Contact Us</a>
  <span class="abs arrow" style="left:42px;top:274px"><svg width="18" height="18" viewBox="0 0 20 20"><path d="M13 3 6 10l7 7" stroke="#222" stroke-width="2.6" fill="none"/></svg></span>
  <span class="abs arrow" style="left:1102px;top:274px"><svg width="18" height="18" viewBox="0 0 20 20"><path d="m7 3 7 7-7 7" stroke="#222" stroke-width="2.6" fill="none"/></svg></span>
</section>

<!-- feature strip -->
<div class="abs strip" style="left:112px;width:365px;background:var(--blue)"></div>
<div class="abs strip" style="left:477px;width:252px;background:var(--orange)"></div>
<div class="abs strip" style="left:729px;width:359px;background:var(--sky)"></div>
<div class="abs feature" style="left:125px">
  <div class="ring" style="border-color:var(--blue)"><svg width="36" height="36" viewBox="0 0 24 24"><path d="M5 3h12a2 2 0 0 1 2 2v16H7a2 2 0 0 1-2-2z" fill="var(--blue)"/><path d="M8 7h8M8 10h8" stroke="#fff" stroke-width="1.5"/></svg></div>
  <small>Get your</small><b style="color:var(--blue)">COACH BOOKS</b>
</div>
<div class="abs feature" style="left:450px">
  <div class="ring" style="border-color:var(--orange)"><svg width="36" height="36" viewBox="0 0 24 24"><rect x="3" y="5" width="18" height="16" rx="2" fill="none" stroke="var(--orange)" stroke-width="2"/><path d="M3 9h18M8 3v4M16 3v4" stroke="var(--orange)" stroke-width="2"/><path d="M7 13h2M11 13h2M15 13h2M7 17h2M11 17h2" stroke="var(--orange)" stroke-width="2"/></svg></div>
  <small>Look at</small><b style="color:var(--orange)">NEXT SCHEDULED</b>
</div>
<div class="abs feature" style="left:775px">
  <div class="ring" style="border-color:var(--sky)"><svg width="38" height="38" viewBox="0 0 24 24" fill="var(--sky)"><circle cx="12" cy="8" r="3.2"/><circle cx="5.5" cy="10" r="2.4"/><circle cx="18.5" cy="10" r="2.4"/><path d="M6.5 19a5.5 5.5 0 0 1 11 0z"/><path d="M1 19a4.5 4.5 0 0 1 5.5-4.4A7 7 0 0 0 5 19zM23 19a4.5 4.5 0 0 0-5.5-4.4A7 7 0 0 1 19 19z"/></svg></div>
  <small>Get a</small><b style="color:var(--sky)">COACH ONLINE</b>
</div>

<!-- about -->
<div class="abs about-photo" role="img" aria-label="Portrait photo of the coach in a bright office"></div>
<div class="abs about-frame"></div>
<div class="abs about-frame-b"></div>
<div class="abs person-name">Renata</div>
<div class="abs person-role">Speech Coach</div>
<h2 class="abs section-title about-title">ABOUT RENATA</h2>
<div class="abs about-copy">
  <p>Renata Brightwell is an Executive Coach for public speaking and all areas of spoken communication.</p>
  <p>Renata delivers highly effective communication workshops and individual coaching services to clients in a diverse range of industries. She provides one-on-one support for foreign executives to increase intelligibility in American English and to adapt to American executive culture. She also works with actors to develop or diminish dialects for performances on stage and film.</p>
</div>
<a href="#" class="abs btn about-btn">More About Me</a>

<!-- services -->
<section class="abs services"></section>
<h2 class="abs section-title services-title">OUR SERVICES</h2>
<svg class="abs" style="left:0;top:1503px" width="1200" height="670" viewBox="0 0 1200 670">
  <g stroke="var(--blue)" stroke-width="3" fill="none">
    <path d="M527 280 L560 330"/><path d="M726 314 L680 360"/><path d="M471 479 L530 440"/><path d="M673 499 L640 460"/>
  </g>
</svg>
<div class="abs hub"><b>brightwell</b><span>voicetutoring</span></div>
<span class="abs dot" style="left:510px;top:1766px;border-color:var(--blue)"><i style="background:var(--sky)"></i></span>
<span class="abs dot" style="left:700px;top:1791px;width:52px;height:52px;border-color:var(--orange)"><i style="background:var(--sky);width:24px;height:24px"></i></span>
<span class="abs dot" style="left:445px;top:1956px;width:52px;height:52px;border-color:var(--orange)"><i style="background:var(--blue);width:24px;height:24px"></i></span>
<span class="abs dot" style="left:656px;top:1985px;border-color:var(--blue)"><i style="background:var(--sky)"></i></span>
<div class="abs svc right-align" style="right:718px;top:1725px;width:420px"><h3 style="color:var(--blue)">COACHING</h3><p>One-on-one, Individual, And Customized To<br>Your Unique Goals, Obstacles, And Challenges.<br>In Person, Or Via Videoconference.</p></div>
<div class="abs svc" style="left:777px;top:1725px;width:420px"><h3 style="color:var(--orange)">ACCENTS</h3><p>Support For Executives From Outside The U.s. To<br>Increase Intelligibility And Diminish Obstacles To<br>Successful Communication In American English.</p></div>
<div class="abs svc right-align" style="right:779px;top:1921px;width:420px"><h3 style="color:var(--orange)">CUSTOM WORKSHOPS</h3><p>Unique, Effective Program Design And Facilitation<br>To Match The Needs Of Executives, Managers,<br>Or Promising Individuals Of Any Level.</p></div>
<div class="abs svc" style="left:726px;top:1952px;width:420px"><h3 style="color:var(--blue)">KEYNOTE SPEECHES</h3><p>Fresh Ways Of Thinking About Speaking And<br>Communication Combined With Practical Tools For<br>Participants Of Your Next Conference Or Event.</p></div>

<!-- voiceover -->
<section class="abs voice">
  <h2 class="abs section-title voice-title" style="top:75px">VOICEOVER</h2>
  <p class="abs voice-copy" style="top:147px">As an award-winning voiceover performer, Renata has worked with producers<br>such as Listenhall.com, Harrow &amp; Pike, Lumen Audio and Spoken Pages.</p>
  <a href="#" class="abs btn" style="left:146px;top:244px;width:474px;background:var(--sky)">FIND OUT MORE AND LISTEN TO SAMPLES HERE</a>
  <a href="#" class="abs btn" style="left:642px;top:244px;width:412px;background:var(--orange)">CLICK HERE TO SEE HER PHOTOGRAPHY</a>
</section>

<!-- training -->
<h2 class="abs section-title train-title">BVT PROVIDES TRAINING,<br>TOOLS, AND TECHNIQUES</h2>
<ul class="abs train-list">
  <li>Executive Presence – Polishing Personal Presentation/Manner</li>
  <li>Addressing and Overcoming Speaking/Communication Anxiety</li>
  <li>Last-Minute Presentation 911</li>
  <li>Media Training</li>
  <li>Modifying Accents for Clarity and Intelligibility</li>
  <li>Communicating Complex/Technical Material to Any Audience</li>
</ul>
<div class="abs video-frame"></div>
<div class="abs video" role="img" aria-label="Video still of the coach speaking in a living room">
  <svg class="abs" style="left:198px;top:121px" width="66" height="66" viewBox="0 0 66 66"><circle cx="33" cy="33" r="30" fill="rgba(0,0,0,.25)" stroke="#fff" stroke-width="3"/><path d="M26 20v26l21-13z" fill="#fff"/></svg>
</div>

<!-- partners -->
<section class="abs partners"></section>
<h2 class="abs section-title partners-title">OUR PARTNER</h2>
<div class="abs logo-card" style="left:95px"><i></i>Fizzco</div>
<div class="abs logo-card" style="left:300px">Ardent</div>
<div class="abs logo-card" style="left:507px">Searchly</div>
<div class="abs logo-card" style="left:709px">Ovalo</div>
<div class="abs logo-card" style="left:917px">Lifeward</div>
<span class="abs slide-arrow" style="left:38px;top:3294px"><svg width="16" height="16" viewBox="0 0 20 20"><path d="M13 3 6 10l7 7" stroke="#fff" stroke-width="3" fill="none"/></svg></span>
<span class="abs slide-arrow" style="left:1101px;top:3294px"><svg width="16" height="16" viewBox="0 0 20 20"><path d="m7 3 7 7-7 7" stroke="#fff" stroke-width="3" fill="none"/></svg></span>

<!-- reviews -->
<div class="abs reviewer" role="img" aria-label="Portrait photo of the reviewing client"></div>
<div class="abs quote">“</div>
<h2 class="abs section-title review-title">CLIENT REVIEWS</h2>
<p class="abs review-copy">Renata showed me how one word or phrase and a certain intonation can influence the outcome of a speech. After one session, I began to reap the rewards of her coaching and after a series of sessions, I have been killing it. Renata is whip-smart, intuitive, analytical and an absolute pleasure to work with. With her invaluable help and patient support, I can now speak concisely and confidently in any setting about what sets my company apart.</p>
<div class="abs review-name">MARTIN DELACOURT</div>
<div class="abs review-role">CEO, Heartline | New York, NY</div>
<div class="abs review-rule"></div>
<div class="abs review-brand"><i></i>Heartline</div>
<span class="abs pager" style="left:229px"></span>
<span class="abs pager" style="left:251px;background:#777"></span>
<span class="abs pager" style="left:273px;background:#777"></span>

<!-- footer -->
<footer class="abs footer">
  <h4 style="left:112px">Renata Brightwell</h4>
  <div class="col-text" style="left:112px;top:100px;width:385px">Public Speaking Consultant<br>Providing highly specialized executive coaching services and program design and facilitation for leadership development, public speaking, and all areas of spoken communication.</div>
  <h4 style="left:558px">Location</h4>
  <div class="f-item" style="left:562px;top:105px">
    <svg width="16" height="22" viewBox="0 0 16 22"><path d="M8 0a8 8 0 0 0-8 8c0 6 8 14 8 14s8-8 8-14a8 8 0 0 0-8-8z" fill="#fff"/><circle cx="8" cy="8" r="3" fill="#121212"/></svg>
    <span>No. 48-1, Section 3,<br>Maple Grove Road,<br>Eastfield District<br>Northport City 2041</span>
  </div>
  <h4 style="left:813px">Contact Us</h4>
  <div class="f-item" style="left:813px;top:105px;align-items:center">
    <svg width="20" height="20" viewBox="0 0 24 24"><path fill="none" stroke="#fff" stroke-width="1.8" d="M6.6 10.8a15.1 15.1 0 0 0 6.6 6.6l2.2-2.2c.3-.3.7-.4 1-.2 1.1.4 2.3.6 3.6.6.6 0 1 .4 1 1V20c0 .6-.4 1-1 1A17 17 0 0 1 3 4c0-.6.4-1 1-1h3.5c.6 0 1 .4 1 1 0 1.3.2 2.5.6 3.6.1.3 0 .7-.2 1z"/></svg>
    <span>718.555.0143</span>
  </div>
  <div class="f-item" style="left:813px;top:150px;align-items:center">
    <svg width="20" height="20" viewBox="0 0 24 24"><rect x="2.5" y="5.5" width="19" height="13" fill="none" stroke="#fff" stroke-width="1.8"/><path d="M3 6l9 7 9-7" stroke="#fff" stroke-width="1.8" fill="none"/></svg>
    <span>info@brightwellvoicetutor.com</span>
  </div>
  <div class="rule"></div>
  <div class="legal" style="left:112px">© Copyrights 2019 | All Rights Reserved</div>
  <div class="legal" style="left:746px">Terms &amp; Conditions</div>
  <div class="legal" style="left:900px">Privacy Policy</div>
  <div class="legal" style="left:1012px">Contact Us</div>
</footer>

</body>
</html>
```